One of a Kind Clean Business Card

We need to design a new business card template for our company. Our company designs and produced merchandising displays. You can see a sample of what we produce on our site www.qorvanexhibits.net. I have uploaded our logo in vector format, as well as a picture of our current business cards. We want a totally different look. We want simple and clean, looking forward to seeing what people create.
Updates

I would like to update the address for Qorvan Display Group Inc. 518 E Tollmere Ln Arlington Heights, IL 60017 Would also note. No QR codes

Industry/Entity Type

Business

Contact Information for Business Card

Need a 1 sided business card designed.

Font styles to use
Serif

Requirements
Must have
• Easy to view; Clean Design
Nice to have
• Features that promote engineering and creativity
Should not have
• Too much clutter, keep it simple

```html
<!DOCTYPE html>
<html lang="en">
<head>
<meta charset="utf-8">
<title>Qorvan Display Group Inc. – Business Card</title>
<link href="https://fonts.googleapis.com/css2?family=Arimo:wght@400&family=Open+Sans:ital,wght@0,400;0,600;1,400;1,600&display=swap" rel="stylesheet">
<style>
  :root {
    --backdrop: #1c1c1c;
    --card: #ffffff;
    --card-shade: #ececec;
    --edge-band: #0f4662;
    --brand-red: #a8192e;
    --ink: #1d1d1d;
    --ink-soft: #3a3a3a;
    --surname: #8a5a22;
    --divider: #9a9a9a;
  }
  * { box-sizing: border-box; margin: 0; padding: 0; }
  html, body {
    width: 1200px;
    height: 982px;
    overflow: hidden;
    background: var(--backdrop);
  }
  .canvas {
    position: relative;
    width: 1200px;
    height: 982px;
  }
  .business-card {
    position: absolute;
    left: 75px;
    top: 191px;
    width: 1050px;
    height: 600px;
    background: radial-gradient(ellipse at 60% 35%, var(--card) 45%, var(--card-shade) 100%);
    overflow: hidden;
  }
  .edge-band {
    position: absolute;
    top: 0;
    width: 24px;
    height: 100%;
    background: var(--edge-band);
  }
  .edge-band--left { left: 0; }
  .edge-band--right { right: 0; }

  .company-name {
    position: absolute;
    left: 92px;
    top: 86px;
    font-family: "Open Sans", sans-serif;
    font-weight: 400;
    font-size: 34px;
    letter-spacing: 0.5px;
    color: var(--brand-red);
  }

  .contact-list {
    position: absolute;
    left: 112px;
    top: 318px;
    list-style: none;
    font-family: "Open Sans", sans-serif;
    font-style: italic;
    font-size: 18px;
    line-height: 31px;
    color: var(--ink-soft);
  }
  .contact-list .label {
    font-weight: 600;
    color: var(--ink);
    margin-right: 4px;
  }

  .divider {
    position: absolute;
    left: 560px;
    top: 300px;
    width: 30px;
    height: 200px;
  }

  .person {
    position: absolute;
    left: 606px;
    top: 352px;
  }
  .person-name {
    font-family: "Arimo", sans-serif;
    font-weight: 400;
    font-size: 46px;
    line-height: 1;
    color: var(--ink);
  }
  .person-name .surname { color: var(--surname); }
  .website {
    margin-top: 14px;
    font-family: "Open Sans", sans-serif;
    font-weight: 600;
    font-size: 17px;
    color: var(--ink);
  }
</style>
</head>
<body>
<main class="canvas">
  <article class="business-card">
    <div class="edge-band edge-band--left"></div>
    <div class="edge-band edge-band--right"></div>

    <h1 class="company-name">Qorvan Display Group Inc.</h1>

    <ul class="contact-list">
      <li><span class="label">O:</span>815-555-0142</li>
      <li><span class="label">C:</span>312-555-0187</li>
      <li><span class="label">E:</span>dverhoff@qorvanexhibits.net</li>
      <li><span class="label">L:</span>518 E Tollmere Ln Arlington Heights, IL 60017</li>
    </ul>

    <svg class="divider" viewBox="0 0 30 200" aria-hidden="true">
      <defs>
        <linearGradient id="divider-fade" x1="0" y1="0" x2="0" y2="1">
          <stop offset="0" stop-color="var(--divider)" stop-opacity="0"/>
          <stop offset="0.5" stop-color="var(--divider)" stop-opacity="1"/>
          <stop offset="1" stop-color="var(--divider)" stop-opacity="0"/>
        </linearGradient>
      </defs>
      <line x1="24" y1="0" x2="6" y2="200" stroke="url(#divider-fade)" stroke-width="2"/>
    </svg>

    <div class="person">
      <p class="person-name">Dale <span class="surname">Verhoff</span></p>
      <p class="website">www.qorvanexhibits.net</p>
    </div>
  </article>
</main>
</body>
</html>
```